Young, dynamic furniture company needs a new business card design

We require a new business card design for our modern furniture company which supplies furniture and appliances to the property and development market.
Oakridge Interiors has become one of the leading furniture & appliance suppliers to the property market withing London. With over 10 years experience, we have increased our business to supply not only private landlords and managing agents, but also property developers, housing associations and local councils.
We offer not only a complete range of furniture which includes beds, wardrobes, dining sets and sofas, but also a high quality, full delivery and assembly service to help you with all our furnishing needs.

Target Market(s)

Private landlords, estate agents, letting agents, property management companies

Industry/Entity Type

Business

Contact Information for Business Card

Name,
Title,
Address,
Mobile,
Telephone,
Fax, Website, email address

Font styles to use
Sans Serif

Colors
3176b5
0555a3
85abd2
cfdeed

Requirements
Must have
• All the above information for each of our staff, along with our logo

```html
<!DOCTYPE html>
<html lang="en">
<head>
<meta charset="utf-8">
<title>Oakridge Interiors – Business Card</title>
<link rel="stylesheet" href="https://fonts.googleapis.com/css2?family=Montserrat:wght@500;700&family=Roboto:wght@400&display=swap">
<style>
  :root {
    --navy: #1f3a6e;
    --ink: #141414;
    --paper: #ffffff;
    --backdrop: #e9ecf0;
    --text-dark: #2b2b2b;
  }
  * { margin: 0; padding: 0; box-sizing: border-box; }
  html, body { width: 1200px; height: 902px; overflow: hidden; background: var(--backdrop); }
  .stage { position: relative; width: 1200px; height: 902px; }
  .card {
    position: absolute; left: 60px; top: 142px;
    width: 940px; height: 537px;
    transform: scale(1.149); transform-origin: 0 0;
    background: var(--paper); border-radius: 22px; overflow: hidden;
    box-shadow: 0 8px 28px rgba(0,0,0,.18);
  }
  .card-shape { position: absolute; inset: 0; }
  .contact-side {
    position: absolute; left: 48px; top: 0; color: var(--paper);
    font-family: "Montserrat", sans-serif; font-weight: 500;
  }
  .person-name { position: absolute; top: 68px; font-size: 31px; font-weight: 700; white-space: nowrap; letter-spacing: .2px; }
  .person-title { position: absolute; top: 101px; font-size: 22px; white-space: nowrap; }
  .address { position: absolute; top: 206px; font-size: 22px; line-height: 33px; white-space: nowrap; }
  .contact-list { position: absolute; top: 288px; list-style: none; font-size: 23px; line-height: 31.5px; white-space: nowrap; }
  .contact-list li { display: flex; align-items: center; gap: 8px; }
  .contact-icon { width: 26px; height: 26px; flex: none; }
  .website { position: absolute; top: 439px; font-size: 21px; white-space: nowrap; }
  .brand-side {
    position: absolute; left: 500px; right: 0; top: 0; bottom: 0;
    font-family: "Roboto", sans-serif; color: var(--text-dark);
  }
  .brand-lockup { position: absolute; left: 0; right: 0; top: 318px; display: flex; justify-content: center; align-items: center; gap: 12px; }
  .brand-mark { width: 22px; height: 22px; background: var(--navy); }
  .brand-name { font-size: 33px; font-weight: 400; color: var(--text-dark); white-space: nowrap; }
  .tagline { position: absolute; left: 0; right: 0; top: 390px; text-align: center; font-size: 17.5px; letter-spacing: .3px; }
</style>
</head>
<body>
<main class="stage">
  <article class="card">
    <svg class="card-shape" viewBox="0 0 940 537" width="940" height="537" aria-hidden="true">
      <path d="M487 0 Q405 268 487 537 H494 Q438 268 494 0 Z" fill="var(--ink)"/>
      <path d="M0 0 H493 Q418 268 490 537 H0 Z" fill="var(--navy)"/>
    </svg>

    <section class="contact-side">
      <h1 class="person-name">DANIEL HART</h1>
      <p class="person-title">Maneger</p>
      <address class="address" style="font-style:normal">Your Address,2nd Ste<br>Maple Falls, Texas 1234, USA</address>
      <ul class="contact-list">
        <li><svg class="contact-icon" viewBox="0 0 26 26"><rect width="26" height="26" rx="4" fill="#fff"/><path d="M8 5 L11 5 L12 9 L10 11 Q12 15 15 16 L17 14 L21 15 L21 18 Q20 21 17 21 Q6 19 5 8 Q5 5 8 5Z" fill="var(--navy)"/></svg>123 456 7890</li>
        <li><svg class="contact-icon" viewBox="0 0 26 26"><rect width="26" height="26" rx="4" fill="#fff"/><rect x="8" y="4" width="10" height="6" fill="var(--navy)"/><rect x="4" y="10" width="18" height="9" rx="1.5" fill="var(--navy)"/><rect x="8" y="16" width="10" height="6" fill="var(--navy)" stroke="#fff" stroke-width="1"/></svg>123 456 7890</li>
        <li><svg class="contact-icon" viewBox="0 0 26 26"><rect width="26" height="26" rx="4" fill="#fff"/><rect x="8" y="3" width="10" height="20" rx="2" fill="var(--navy)"/><rect x="10" y="6" width="6" height="7" fill="#fff"/></svg>123 456 7890</li>
        <li><svg class="contact-icon" viewBox="0 0 26 26"><rect width="26" height="26" rx="4" fill="#fff"/><rect x="4" y="7" width="18" height="12" fill="var(--navy)"/><path d="M4 7 L13 14 L22 7 M4 19 L10 13 M22 19 L16 13" stroke="#fff" stroke-width="1.4" fill="none"/></svg>your@yourcompany.com</li>
      </ul>
      <p class="website">www.yourcompany.com</p>
    </section>

    <section class="brand-side">
      <div class="brand-lockup">
        <span class="brand-mark"></span>
        <span class="brand-name">OAKRIDGE INTERIORS</span>
      </div>
      <p class="tagline">TRADE FURNITURE SOLUTIONS</p>
    </section>
  </article>
</main>
</body>
</html>
```